Real Estate investment company needs billboard designs

This is our website: https://brightlanepropertygroup.com/
We are looking for some billboard concepts that uses our CEO in the design. I have attached some images and 1 billboard design that someone in our industry uses, but we don't want it exactly like his.

Industry/Entity Type

real estate

Colors

Designer to choose colors to be used in the design.

Requirements
Must have
• Company colors from websiute

```html
<!DOCTYPE html>
<html lang="en">
<head>
<meta charset="utf-8">
<title>Brightlane Property Group – Billboard</title>
<link rel="stylesheet" href="https://fonts.googleapis.com/css2?family=Montserrat:wght@700;800&display=swap">
<style>
  :root {
    --page-bg: #d8d8d8;
    --navy-deep: #14152f;
    --navy: #1d1f45;
    --red: #e8141b;
    --red-dark: #7a0d1c;
    --white: #ffffff;
    --denim-light: #a9bfdc;
    --denim: #6f87a8;
    --icon-dark: #2a1420;
  }
  html, body {
    margin: 0;
    width: 1031px;
    height: 1200px;
    overflow: hidden;
    background: var(--page-bg);
  }
  .canvas {
    position: relative;
    width: 1031px;
    height: 1200px;
  }
  .billboard {
    position: absolute;
    left: 36px;
    top: 378px;
    width: 960px;
    height: 444px;
    box-shadow: 0 6px 14px rgba(0,0,0,0.35);
  }
  .billboard svg { display: block; width: 100%; height: 100%; }
  .headline {
    font-family: "Montserrat", sans-serif;
    font-weight: 800;
    fill: var(--white);
  }
  .brand-name {
    font-family: "Montserrat", sans-serif;
    font-weight: 800;
    fill: var(--white);
    letter-spacing: 1px;
  }
  .web-address {
    font-family: "Montserrat", sans-serif;
    font-weight: 700;
    fill: var(--white);
  }
</style>
</head>
<body>
<main class="canvas">
  <section class="billboard" aria-label="Brightlane Property Group billboard">
    <svg viewBox="0 0 1492 690" xmlns="http://www.w3.org/2000/svg">
      <defs>
        <linearGradient id="bg-fade" x1="0" y1="0" x2="1" y2="1">
          <stop offset="0" stop-color="var(--navy-deep)"/>
          <stop offset="0.6" stop-color="var(--navy)"/>
          <stop offset="1" stop-color="var(--navy-deep)"/>
        </linearGradient>
        <linearGradient id="band-fade" x1="0" y1="0" x2="1" y2="0">
          <stop offset="0" stop-color="var(--red)"/>
          <stop offset="0.5" stop-color="var(--red)" stop-opacity="0.85"/>
          <stop offset="1" stop-color="var(--red-dark)" stop-opacity="0"/>
        </linearGradient>
        <linearGradient id="stripe-fade" x1="0" y1="0" x2="1" y2="1">
          <stop offset="0" stop-color="var(--red-dark)"/>
          <stop offset="1" stop-color="var(--red)"/>
        </linearGradient>
        <linearGradient id="portrait-tone" x1="0" y1="0" x2="0" y2="1">
          <stop offset="0" stop-color="var(--denim)"/>
          <stop offset="0.5" stop-color="var(--denim-light)"/>
          <stop offset="1" stop-color="var(--denim)"/>
        </linearGradient>
      </defs>

      <rect class="backdrop" width="1492" height="690" fill="url(#bg-fade)"/>

      <polygon class="accent-stripe" points="905,0 1165,0 1450,325 1210,330" fill="url(#stripe-fade)"/>
      <polygon class="accent-corner" points="880,690 925,640 925,690" fill="var(--red)"/>

      <g class="brand">
        <rect class="brand-mark" x="75" y="92" width="38" height="38" fill="var(--red)"/>
        <text class="brand-name" x="128" y="128" font-size="44">BRIGHTLANE</text>
        <text class="brand-name" x="128" y="180" font-size="44">PROPERTY GROUP</text>
      </g>

      <text class="headline" x="62" y="350" font-size="150" textLength="985" lengthAdjust="spacingAndGlyphs">GUARANTEED</text>
      <text class="headline" x="62" y="490" font-size="150" textLength="518" lengthAdjust="spacingAndGlyphs">OFFER</text>

      <rect class="web-band" x="0" y="526" width="920" height="94" fill="url(#band-fade)"/>
      <g class="globe-icon" fill="none" stroke="var(--icon-dark)" stroke-width="4">
        <circle cx="88" cy="573" r="19"/>
        <ellipse cx="88" cy="573" rx="8" ry="19"/>
        <line x1="69" y1="573" x2="107" y2="573"/>
      </g>
      <text class="web-address" x="133" y="589" font-size="48" textLength="720" lengthAdjust="spacingAndGlyphs">brightlanepropertygroup.com</text>

      <path class="ceo-portrait" d="M1100,15 H1310 V280 H1492 V690 H925 V380 H1070 V280 H1100 Z" fill="url(#portrait-tone)"
            role="img" aria-label="Photo of the company CEO, arms crossed, wearing a light denim shirt"/>
    </svg>
  </section>
</main>
</body>
</html>
```